Tollin Waste Website Design

Our new start-up needs a website design. We plan to help businesses find more sustainable ways to manage their waste. Our initial website aims to gather contact data from potential business customers and comprehensive information from waste facilities and waste transporters. We have a logo design (attached) which we would like included in the website design. I have also attached a number of pages that describe what information should appear on each page as well as a web design brief file that describes the look we are after.

```html
<!DOCTYPE html>
<html lang="en">
<head>
<meta charset="UTF-8">
<title>Tollin Waste – Website Design</title>
<link href="https://fonts.googleapis.com/css2?family=Open+Sans:wght@400;700&family=Poppins:wght@400;500&family=Roboto:wght@400&display=swap" rel="stylesheet">
<style>
  :root{
    --page-bg:#d3e7b8;
    --brand-green:#6aa42a;
    --brand-green-light:#7dc02d;
    --ink:#1b1b1b;
    --ink-soft:#3a3a3a;
    --white:#ffffff;
    --footer-bg:rgba(30,32,30,0.88);
    --circle-fill:rgba(20,24,18,0.72);
    --overlay:rgba(0,0,0,0.58);
  }
  *{box-sizing:border-box;margin:0;padding:0}
  html,body{width:900px;height:1200px;overflow:hidden}
  body{background:var(--page-bg);position:relative;font-family:'Poppins',sans-serif}

  .screen{position:absolute;left:39px;width:822px;height:496px;overflow:hidden;
    box-shadow:0 2px 8px rgba(0,0,0,0.25)}
  .screen--home{top:52px}
  .screen--signup{top:620px}

  .hero-photo{position:absolute;inset:0;
    background:
      radial-gradient(ellipse at 50% 70%, rgba(196,120,40,0.75) 0%, rgba(120,90,40,0.35) 35%, transparent 60%),
      linear-gradient(180deg,#c9cfcf 0%,#6f8a4a 22%,#4c6a2e 45%,#3f4a34 70%,#2d2f2c 100%);}

  .site-header{position:absolute;top:0;left:0;right:0;height:70px}
  .brand{position:absolute;left:62px;top:22px;display:flex;align-items:center;gap:8px}
  .brand-dot{width:26px;height:26px;border-radius:50%;background:var(--brand-green-light)}
  .brand-name{font-family:'Poppins',sans-serif;font-weight:500;font-size:20px;color:var(--white)}

  .main-nav{position:absolute;left:226px;top:26px;display:flex;gap:14px;
    font-size:12px;color:var(--white)}
  .social{position:absolute;left:663px;top:25px;display:flex;gap:6px}
  .social span{width:20px;height:20px;border:1px solid var(--white);border-radius:50%}

  .hero-title{position:absolute;top:118px;left:0;right:0;text-align:center;
    font-family:'Open Sans',sans-serif;font-weight:700;font-size:37px;color:var(--white);letter-spacing:-0.5px}
  .hero-sub{position:absolute;top:166px;left:0;right:0;text-align:center;
    font-family:'Open Sans',sans-serif;font-size:27px;color:var(--white)}

  .role-card{position:absolute;top:236px;width:128px;height:128px;border-radius:50%;
    background:var(--circle-fill);border:5px solid var(--brand-green-light);
    display:flex;flex-direction:column;align-items:center;justify-content:center;
    color:var(--white);font-size:15px;line-height:18px;text-align:center}
  .role-card svg{margin-bottom:6px}
  .role-card--producers{left:178px}
  .role-card--facilities{left:341px}
  .role-card--transporters{left:503px}

  .site-footer{position:absolute;left:0;right:0;bottom:0;height:60px;background:var(--footer-bg);
    border-top:1px solid rgba(255,255,255,0.25);
    display:flex;align-items:center;justify-content:center;
    font-family:'Roboto',sans-serif;font-size:12px;color:var(--white)}

  .overlay{position:absolute;inset:0;background:var(--overlay)}

  .signup-modal{position:absolute;left:142px;top:100px;width:538px;height:286px;
    background:var(--white);border-radius:12px;text-align:center}
  .modal-close{position:absolute;left:506px;top:12px;width:21px;height:21px}
  .modal-brand{position:absolute;top:34px;left:0;right:0;display:flex;justify-content:center;align-items:center;gap:10px}
  .modal-brand .brand-dot{width:40px;height:40px}
  .modal-brand .brand-name{font-size:32px;color:var(--ink-soft)}
  .modal-title{position:absolute;top:98px;left:0;right:0;font-weight:500;font-size:24px;color:var(--ink)}
  .modal-text{position:absolute;top:132px;left:0;right:0;font-family:'Roboto',sans-serif;
    font-size:13px;line-height:22px;color:var(--ink-soft)}
  .signup-form{position:absolute;left:53px;top:198px;width:432px;height:44px;
    border:1px solid #555;border-radius:22px;display:flex;align-items:center;justify-content:space-between;padding:0 3px 0 19px}
  .signup-form input{border:none;outline:none;font-family:'Roboto',sans-serif;font-size:12px;color:var(--ink);background:transparent;width:300px}
  .signup-form input::placeholder{color:var(--ink)}
  .signup-form button{width:80px;height:36px;border:none;border-radius:18px;background:var(--brand-green);
    color:var(--white);font-family:'Poppins',sans-serif;font-size:16px}
</style>
</head>
<body>

<section class="screen screen--home">
  <div class="hero-photo" role="img" aria-label="Street lined with trees, an orange garbage truck and metal waste bins"></div>
  <header class="site-header">
    <div class="brand"><span class="brand-dot"></span><span class="brand-name">Tollin Waste</span></div>
    <nav class="main-nav"><span>About us</span><span>What we do</span><span>Resources</span><span>Contact us</span></nav>
    <div class="social"><span></span><span></span><span></span><span></span></div>
  </header>
  <h1 class="hero-title">WELCOME TO TOLLIN WASTE</h1>
  <p class="hero-sub">Take control of your waste here</p>

  <div class="role-card role-card--producers">
    <svg width="22" height="28" viewBox="0 0 22 28" fill="none" stroke="#7dc02d" stroke-width="2.2">
      <path d="M2 6h18M8 6V3h6v3M4 6l2 20h10l2-20M9 10v12M13 10v12"/>
    </svg>
    Waste<br>Producers
  </div>
  <div class="role-card role-card--facilities">
    <svg width="28" height="26" viewBox="0 0 28 26" fill="none" stroke="#7dc02d" stroke-width="3">
      <path d="M14 3a10 10 0 1 1-9.5 7"/><path d="M2 6l3 4.5 4.5-3" stroke-width="2.4"/>
    </svg>
    Waste<br>Facilities
  </div>
  <div class="role-card role-card--transporters">
    <svg width="40" height="24" viewBox="0 0 40 24" fill="#7dc02d">
      <rect x="1" y="3" width="25" height="14" rx="1"/>
      <path d="M27 7h7l5 6v4H27z"/>
      <circle cx="8" cy="20" r="3"/><circle cx="21" cy="20" r="3"/><circle cx="33" cy="20" r="3"/>
    </svg>
    Waste<br>Transporters
  </div>

  <footer class="site-footer">Copyright © 2018. All Rights Reserved</footer>
</section>

<section class="screen screen--signup">
  <div class="hero-photo" role="img" aria-label="Street lined with trees, an orange garbage truck and metal waste bins"></div>
  <header class="site-header">
    <div class="brand"><span class="brand-dot"></span><span class="brand-name">Tollin Waste</span></div>
    <nav class="main-nav"><span>About us</span><span>What we do</span><span>Resources</span><span>Contact us</span></nav>
    <div class="social"><span></span><span></span><span></span><span></span></div>
  </header>
  <footer class="site-footer">Copyright © 2018. All Rights Reserved</footer>
  <div class="overlay"></div>

  <div class="signup-modal">
    <svg class="modal-close" viewBox="0 0 21 21" fill="none" stroke="#222" stroke-width="1.2">
      <circle cx="10.5" cy="10.5" r="9.8"/><path d="M6.5 6.5l8 8M14.5 6.5l-8 8"/>
    </svg>
    <div class="modal-brand"><span class="brand-dot"></span><span class="brand-name">Tollin Waste</span></div>
    <h2 class="modal-title">Welcome to TOLLIN Waste.</h2>
    <p class="modal-text">We are just getting started. Please register your email address<br>to receive updates from us</p>
    <form class="signup-form">
      <input type="email" placeholder="Email address">
      <button type="button">Signup</button>
    </form>
  </div>
</section>

</body>
</html>
```